Etiketten-Design für Kräuterbonbon-Metalldose
Katrin Wolber hat sehr viel Talent. Das Design ist absolut kreativ.
Zielgruppe
Unsere Firma FelvoNat verkauft verschiedene Sorten Kräuterbonbons.
Wir brauchen ein Etikett, dass auf eine Metall-Dose (Durchmesser 10 cam, Höhe ca. 3 cm) geklebt wird.
Zielgruppe: jung-alt
Aufgabenstellung
Der Name unserer Kräuterbonbons ist Moospille.
Wir möchten, dass unsere Kunden, wenn sie das Etikett sehen einen Bezug zur Schweiz herstellen können.
Wir verwenden für unsere Bonbons unterschiedliche Kräuter für verschiedene Anwendungen:
Konkret sind erstmal 4 Dosen geplant:
-Kräutermischung aus 16 Kräuter gegen Husten
-Salbei gegen Halsschmerzen
-Anis gegen Magenschmerzen
-Zitrone/Ingwer für die Nerven
Vorderseite: Produktbeschreibung
Rückseite: unsere Herstellerangaben
Größenangaben der Dose: Durchmesser 10 cm, Höhe ca. 3 cm
Im Anhang habe ich Ihnen noch weitere/ genauere Informationen zur Verfügung bereitgestellt!

```html
<!DOCTYPE html>
<html lang="de">
<head>
<meta charset="utf-8">
<title>Moospille – Etiketten für Kräuterbonbon-Dosen</title>
<link rel="stylesheet" href="https://fonts.googleapis.com/css2?family=Montserrat:wght@400;600&family=Oswald:wght@600&display=swap">
<style>
  :root{
    --forest:#1f4a26;
    --paper:#ffffff;
    --lemon-top:#d9d37c;
    --lemon-bottom:#aeaa2b;
    --herbs-top:#d7e6b2;
    --herbs-bottom:#6b7a6b;
    --anise-top:#a874a8;
    --anise-text:#6a1f6a;
    --anise-bottom:#c691c6;
    --sage-top:#abd9c7;
    --sage-bottom:#71a69e;
  }
  *{margin:0;padding:0;box-sizing:border-box}
  html,body{width:1200px;height:891px;overflow:hidden;background:var(--paper)}
  .canvas{position:relative;width:1200px;height:891px;background:var(--paper)}

  .botanical-backdrop{
    position:absolute;left:50px;top:120px;width:1100px;height:400px;
    background:radial-gradient(ellipse at center, rgba(220,220,220,.45) 0%, rgba(235,235,235,.25) 55%, rgba(255,255,255,0) 75%);
  }

  .brand-banner{
    position:absolute;left:336px;top:0;width:497px;height:283px;
    background:var(--forest);
    border-bottom-left-radius:50% 60px;
    border-bottom-right-radius:50% 60px;
    text-align:center;color:var(--paper);
  }
  .brand-name{
    margin-top:112px;
    font-family:"Montserrat",sans-serif;font-weight:600;
    font-size:54px;letter-spacing:0;line-height:1;
  }
  .brand-tagline{
    margin-top:24px;
    font-family:"Montserrat",sans-serif;font-weight:400;
    font-size:20px;letter-spacing:1px;line-height:1;
  }

  .label{
    position:absolute;top:486px;width:228px;height:228px;border-radius:50%;
    overflow:hidden;background:var(--paper);
    box-shadow:0 0 0 1px #e2e2e2;
  }
  .label--lemon{left:109px}
  .label--herbs{left:359px}
  .label--anise{left:619px}
  .label--sage{left:870px}

  .label-art{
    position:absolute;left:0;top:40px;width:228px;height:125px;
    background:linear-gradient(180deg, rgba(235,235,235,.2), rgba(225,225,225,.55));
  }
  .label-banner{
    position:absolute;left:47px;top:0;width:134px;height:70px;
    background:var(--forest);color:var(--paper);text-align:center;
    border-bottom-left-radius:50% 16px;border-bottom-right-radius:50% 16px;
  }
  .label-brand{
    margin-top:25px;
    font-family:"Montserrat",sans-serif;font-weight:600;font-size:15px;line-height:1;
  }
  .label-tagline{
    margin-top:6px;font-family:"Montserrat",sans-serif;font-weight:400;
    font-size:7px;letter-spacing:.4px;line-height:1;
  }

  .variety{
    position:absolute;left:0;top:165px;width:228px;height:22px;
    border-top:2px solid rgba(255,255,255,.7);
    font-family:"Oswald",sans-serif;font-weight:600;font-size:15px;letter-spacing:2.5px;
    line-height:20px;text-align:center;color:var(--forest);
  }
  .use{
    position:absolute;left:0;top:190px;width:228px;height:40px;
    font-family:"Oswald",sans-serif;font-weight:600;font-size:8px;letter-spacing:1.6px;
    line-height:11px;text-align:center;color:var(--paper);padding-top:5px;
  }
  .label--lemon .variety{background:var(--lemon-top)}
  .label--lemon .use{background:var(--lemon-bottom);padding-top:8px}
  .label--herbs .variety{background:var(--herbs-top)}
  .label--herbs .use{background:var(--herbs-bottom)}
  .label--anise .variety{background:var(--anise-top);color:var(--anise-text)}
  .label--anise .use{background:var(--anise-bottom)}
  .label--sage .variety{background:var(--sage-top)}
  .label--sage .use{background:var(--sage-bottom)}
</style>
</head>
<body>
<main class="canvas">
  <div class="botanical-backdrop" role="img" aria-label="Zarte grau gezeichnete Kräuterzweige als Hintergrund"></div>

  <header class="brand-banner">
    <p class="brand-name">Moospille</p>
    <p class="brand-tagline">Traditional Swiss Formula</p>
  </header>

  <section class="label label--lemon">
    <div class="label-art" role="img" aria-label="Feine Kräuterzeichnung"></div>
    <div class="label-banner">
      <p class="label-brand">Moospille</p>
      <p class="label-tagline">Traditional Swiss Formula</p>
    </div>
    <div class="variety">ZITRONE &amp; INGWER</div>
    <div class="use">FÜR DIE NERVEN</div>
  </section>

  <section class="label label--herbs">
    <div class="label-art" role="img" aria-label="Feine Kräuterzeichnung"></div>
    <div class="label-banner">
      <p class="label-brand">Moospille</p>
      <p class="label-tagline">Traditional Swiss Formula</p>
    </div>
    <div class="variety">16 KRÄUTER</div>
    <div class="use">KRÄUTERMISCHUNG<br>GEGEN HUSTEN</div>
  </section>

  <section class="label label--anise">
    <div class="label-art" role="img" aria-label="Feine Kräuterzeichnung"></div>
    <div class="label-banner">
      <p class="label-brand">Moospille</p>
      <p class="label-tagline">Traditional Swiss Formula</p>
    </div>
    <div class="variety">ANIS</div>
    <div class="use">WOHLTUEND BEI<br>MAGENSCHMERZEN</div>
  </section>

  <section class="label label--sage">
    <div class="label-art" role="img" aria-label="Feine Kräuterzeichnung"></div>
    <div class="label-banner">
      <p class="label-brand">Moospille</p>
      <p class="label-tagline">Traditional Swiss Formula</p>
    </div>
    <div class="variety">SALBEI</div>
    <div class="use">WOHLTUEND BEI<br>HALSSCHMERZEN</div>
  </section>
</main>
</body>
</html>
```